Wed site for biomedical device startup

We need a generic website for a medical device startup. I will provide examples below of websites from other companies that can serve as models for what we are looking for. The startup is for a device that can non invasively measure blood flow in the brain using light. The application is to detect the type of stroke someone is having before they get to the hospital so treatment can be started right away. This saves patients upto hours of delayed treatment. Patients will be able to recover from stroke much better and faster as a result. I have attached an AI generated illustration of what the device will ultimately look like for reference.

https://www.372clinicaltech.com
https://vextalune.com

Target Market(s)

Biomedical, medical device, investors of biomedical device startups

Industry/Entity Type

Biomedical

Coding

Coded - Design and coding required

Number of Pages Required

4 page

Requirements
Must have
• same section and section headings as example websites listed above
Nice to have
• similar to example websites listed above. Prefer a darker website over a lighter one. Perhaps dark blues to go with logo colors. A moving background image element at top of landing page could be cool. Something indicative of heartbeat, or neurons, or blood flow.

```html
<!DOCTYPE html>
<html lang="en">
<head>
<meta charset="utf-8">
<title>KLARO – Non-invasive Blood Flow Monitoring</title>
<link href="https://fonts.googleapis.com/css2?family=Michroma&family=Roboto:wght@400;500;700&display=swap" rel="stylesheet">
<style>
:root{
  --navy-900:#06042e;
  --navy-800:#0b0838;
  --navy-700:#1b1852;
  --indigo-600:#2c2870;
  --indigo-500:#4a4496;
  --cyan:#2bb8ea;
  --purple:#8a2be2;
  --blue-btn:#3f5ff2;
  --white:#ffffff;
  --text-soft:#dcdcf0;
  --deco-blue:#1f3f8a;
}
*{box-sizing:border-box;margin:0;padding:0}
html,body{width:1200px;height:4170px;overflow:hidden}
body{background:var(--navy-900);font-family:"Roboto",Arial,sans-serif;color:var(--white);position:relative}
.abs{position:absolute}
.display{font-family:"Michroma",Arial,sans-serif;font-weight:400;letter-spacing:2px;text-transform:uppercase}
.accent{color:var(--cyan)}
.rule{position:absolute;height:2px;background:var(--cyan)}
.btn{position:absolute;display:flex;align-items:center;justify-content:center;border-radius:20px;
  background:linear-gradient(90deg,var(--purple),var(--blue-btn));color:var(--white);
  font-size:12px;font-weight:700;letter-spacing:.3px;text-transform:uppercase;
  box-shadow:0 4px 10px rgba(100,90,255,.45)}
.copy{position:absolute;font-size:14px;line-height:24px;color:var(--text-soft);text-align:justify}
.photo{position:absolute;border-radius:10px}
.deco{position:absolute;border-radius:10px}

/* header */
.site-header{left:0;top:0;width:1200px;height:78px;background:var(--navy-800);border-bottom:1px solid #1c1a55}
.brand-name{font-family:"Roboto",Arial,sans-serif;font-weight:500;color:var(--white);letter-spacing:1px}
.main-nav a{position:absolute;top:29px;font-size:13px;font-weight:500;color:var(--white);text-decoration:none}
.main-nav a.active{color:var(--cyan)}

/* hero */
.hero{left:0;top:78px;width:1200px;height:560px;
  background:radial-gradient(ellipse at 50% 15%,#8a83d6 0%,#5e56b0 30%,#39327e 65%,#221c5c 100%)}
.slide-arrow{position:absolute;width:38px;height:38px;border-radius:50%;background:var(--white);display:flex;align-items:center;justify-content:center}

/* sections */
.about{left:0;top:638px;width:1200px;height:602px;background:var(--navy-900)}
.innovation{left:0;top:1240px;width:1200px;height:708px;background:radial-gradient(ellipse at 30% 40%,#36317a 0%,#27225f 55%,#1d1850 100%)}
.help{left:0;top:1948px;width:1200px;height:518px;background:var(--navy-900)}
.explainer{left:0;top:2466px;width:1200px;height:400px;background:radial-gradient(ellipse at 50% 40%,#332e78 0%,#25205e 60%,#1a1550 100%)}
.team{left:0;top:2866px;width:1200px;height:979px;background:var(--navy-900)}
.site-footer{left:0;top:3845px;width:1200px;height:325px;background:radial-gradient(ellipse at 50% 30%,#2c2870 0%,#1d1a55 70%,#151248 100%)}

.feature-icon{position:absolute;width:91px;height:91px;border-radius:8px;background:linear-gradient(135deg,#4a2a9c,#2a2470);display:flex;align-items:center;justify-content:center}
.feature-title{position:absolute;font-size:19px;font-weight:700}
.feature-text{position:absolute;font-size:14px;line-height:25px;color:var(--text-soft)}

.member-ring{position:absolute;width:234px;height:234px;border-radius:50%;border:2px solid #6a3be0;box-shadow:0 0 18px rgba(120,80,255,.45)}
.member-photo{position:absolute;left:12px;top:12px;width:206px;height:206px;border-radius:50%;background:linear-gradient(180deg,#d9d9de,#9fa0aa)}
.member-name{position:absolute;font-size:19px;font-weight:500}
.member-role{position:absolute;font-size:14px;color:var(--text-soft)}
.toggle{position:absolute;width:38px;height:38px;border-radius:50%;background:#1d1a5a;display:flex;align-items:center;justify-content:center}

.contact-card{left:144px;top:3432px;width:912px;height:323px;background:#141148;border-radius:12px}
.contact-line{position:absolute;left:703px;font-size:20px;color:var(--white)}
.contact-icon{position:absolute;left:652px}

.footer-nav{position:absolute;top:4018px;left:0;width:1200px;display:flex;justify-content:center;gap:20px;font-size:15px;font-weight:500}
.footer-nav span.sep{color:var(--text-soft)}
</style>
</head>
<body>

<header class="abs site-header">
  <div class="abs brand-name" style="left:146px;top:19px;font-size:34px;line-height:40px;">KLARO</div>
  <nav class="main-nav">
    <a class="active" style="left:415px">HOME</a>
    <a style="left:481px">ABOUT</a>
    <a style="left:551px">TECHNOLOGY</a>
    <a style="left:665px">PUBLICATIONS</a>
    <a style="left:786px">CONTACT</a>
  </nav>
  <svg class="abs" style="left:880px;top:29px" width="15" height="15" viewBox="0 0 15 15"><circle cx="6" cy="6" r="4.5" stroke="#fff" stroke-width="2" fill="none"/><line x1="9.5" y1="9.5" x2="14" y2="14" stroke="#fff" stroke-width="2"/></svg>
  <div class="btn" style="left:913px;top:18px;width:143px;height:36px;font-size:12px;">Get a Quote</div>
</header>

<section class="abs hero" role="img" aria-label="Close-up background of flowing red blood cells tinted violet">
  <div class="abs display" style="left:0;width:1200px;top:202px;text-align:center;font-size:18px;letter-spacing:2px;">Welcome to</div>
  <div class="abs display" style="left:0;width:1200px;top:226px;text-align:center;font-size:72px;line-height:86px;letter-spacing:6px;">KLARO</div>
  <div class="btn" style="left:528px;top:327px;width:142px;height:35px;">Get Started</div>
  <div class="slide-arrow" style="left:62px;top:261px"><svg width="12" height="12" viewBox="0 0 12 12"><path d="M8 1 3 6l5 5" stroke="#222" stroke-width="2" fill="none"/></svg></div>
  <div class="slide-arrow" style="left:1108px;top:261px"><svg width="12" height="12" viewBox="0 0 12 12"><path d="M4 1l5 5-5 5" stroke="#222" stroke-width="2" fill="none"/></svg></div>
</section>

<section class="abs about">
  <div class="deco" style="left:314px;top:69px;width:212px;height:60px;background:var(--deco-blue)"></div>
  <div class="deco" style="left:115px;top:366px;width:60px;height:116px;background:linear-gradient(180deg,#3a3aa0,#6a1fc0)"></div>
  <div class="photo" role="img" aria-label="Patient wearing forehead sensor pads with handheld monitor showing waveforms" style="left:142px;top:102px;width:421px;height:413px;background:linear-gradient(135deg,#d9c3b4,#8d776b 55%,#2e3440)"></div>
  <h2 class="abs display" style="left:622px;top:100px;font-size:40px;">About <span class="accent">KLARO</span></h2>
  <div class="rule" style="left:622px;top:155px;width:92px"></div>
  <p class="copy" style="left:622px;top:172px;width:434px;">Lorem ipsum dolor sit amet, consectetur adipiscing elit, sed do eiusmod tempor incididunt ut labore et dolore magna aliqua. Ut enim ad minim veniam, quis nostrud exercitation ullamco laboris nisi ut aliquip ex ea commodo consequat. Duis aute irure dolor in reprehenderit in voluptate velit esse cillum dolore eu fugiat nulla pariatur. Excepteur sint occaecat cupidatat non proident, sunt in culpa qui officia deserunt mollit anim id est laborum.</p>
  <p class="copy" style="left:622px;top:364px;width:434px;">Lorem ipsum dolor sit amet, consectetur adipiscing elit, sed do eiusmod tempor incididunt ut labore et dolore magna aliqua. Ut enim ad minim veniam, quis nostrud exercitation ullamco laboris nisi ut aliquip ex ea commodo consequat.</p>
  <div class="btn" style="left:622px;top:476px;width:142px;height:35px;">Learn More</div>
</section>

<section class="abs innovation">
  <h2 class="abs display" style="left:0;width:1200px;top:72px;text-align:center;font-size:38px;line-height:46px;">Innovative Blood<br><span class="accent">Loss Monitoring</span></h2>
  <div class="rule" style="left:555px;top:177px;width:91px"></div>

  <div class="feature-icon" style="left:144px;top:238px">
    <svg width="56" height="50" viewBox="0 0 56 50" fill="none" stroke="#fff" stroke-width="2"><rect x="3" y="3" width="50" height="34" rx="2"/><path d="M20 44h16M28 37v7M10 12h14M10 18h14M10 24h10M34 26v-6M40 26v-12M46 26v-9"/></svg>
  </div>
  <div class="feature-title" style="left:254px;top:244px">Portable Monitoring</div>
  <div class="feature-text" style="left:254px;top:276px;width:330px">Lorem ipsum dolor sit amet, consectetur adipisc ing elit, sed do eiusmod tempor</div>

  <div class="feature-icon" style="left:144px;top:366px">
    <svg width="56" height="56" viewBox="0 0 56 56" fill="none" stroke="#fff" stroke-width="2"><rect x="14" y="4" width="28" height="40" rx="3"/><path d="M20 12h16M20 18h16"/><circle cx="25" cy="34" r="9"/><path d="M32 40l12 12"/></svg>
  </div>
  <div class="feature-title" style="left:254px;top:372px">Real-time Alerts</div>
  <div class="feature-text" style="left:254px;top:404px;width:330px">Lorem ipsum dolor sit amet, consectetur adipisc ing elit, sed do eiusmod tempor</div>

  <div class="feature-icon" style="left:144px;top:494px">
    <svg width="56" height="56" viewBox="0 0 56 56" fill="none" stroke="#fff" stroke-width="2"><circle cx="30" cy="12" r="7"/><path d="M18 34c2-8 22-8 24 0"/><path d="M6 44l10-6h12l-2 5H18M16 50l16-6 14-10"/></svg>
  </div>
  <div class="feature-title" style="left:254px;top:500px">Patient-Centered</div>
  <div class="feature-text" style="left:254px;top:532px;width:330px">Lorem ipsum dolor sit amet, consectetur adipisc ing elit, sed do eiusmod tempor</div>

  <div class="deco" style="left:816px;top:206px;width:210px;height:50px;background:var(--deco-blue)"></div>
  <div class="deco" style="left:615px;top:500px;width:76px;height:119px;background:linear-gradient(180deg,#3a3aa0,#6a1fc0)"></div>
  <div class="photo" role="img" aria-label="Lab technician in protective gear working at a patient monitor" style="left:635px;top:228px;width:421px;height:373px;background:linear-gradient(135deg,#e6eaf0,#9aa6b8 50%,#4f5d74)"></div>
</section>

<section class="abs help">
  <div class="abs" role="img" aria-label="Two scientists in lab coats working at a microscope in a bright laboratory" style="left:0;top:0;width:820px;height:518px;background:linear-gradient(90deg,#8aa3d8 0%,#5a74b8 45%,#2a3585 75%,rgba(6,4,46,0) 100%)"></div>
  <h2 class="abs display" style="left:622px;top:112px;font-size:40px;">How We <span class="accent">Help</span></h2>
  <div class="rule" style="left:622px;top:166px;width:92px"></div>
  <p class="copy" style="left:622px;top:183px;width:434px;">Lorem ipsum dolor sit amet, consectetur adipiscing elit, sed do eiusmod tempor incididunt ut labore et dolore magna aliqua. Ut enim ad minim veniam, quis nostrud exercitation ullamco laboris nisi ut aliquip ex ea commodo consequat. Duis aute irure dolor in reprehenderit in voluptate velit esse cillum dolore eu fugiat nulla pariatur. Excepteur sint occaecat cupidatat non proident, sunt in culpa qui officia deserunt mollit anim id est laborum.</p>
  <div class="btn" style="left:622px;top:367px;width:142px;height:35px;">Learn More</div>
</section>

<section class="abs explainer">
  <h2 class="abs display" style="left:0;width:1200px;top:80px;text-align:center;font-size:40px;">Lumascan <span class="accent">Explained</span></h2>
  <div class="rule" style="left:555px;top:137px;width:91px"></div>
  <p class="copy" style="left:186px;top:160px;width:828px;text-align:center;">Lorem ipsum dolor sit amet, consectetur adipiscing elit, sed do eiusmod tempor incididunt ut labore et dolore magna aliqua. Ut enim ad minim veniam, quis nostrud exercitation ullamco laboris nisi ut aliquip ex ea commodo consequat. Duis aute irure dolor in reprehenderit in voluptate velit esse cillum dolore eu fugiat nulla pariatur. Excepteur sint occaecat cupidatat non proident, sunt in culpa qui officia deserunt mollit anim id est laborum.</p>
  <div class="btn" style="left:529px;top:277px;width:142px;height:35px;">Learn More</div>
</section>

<section class="abs team">
  <h2 class="abs display" style="left:0;width:1200px;top:72px;text-align:center;font-size:40px;">Our <span class="accent">Team</span></h2>
  <div class="rule" style="left:555px;top:133px;width:91px"></div>

  <div class="member-ring" style="left:179px;top:168px"><div class="member-photo" role="img" aria-label="Portrait of team member"></div></div>
  <div class="member-name" style="left:180px;top:416px">John Doe</div>
  <div class="member-role" style="left:180px;top:444px">Company name</div>
  <div class="toggle" style="left:357px;top:419px"><svg width="12" height="8" viewBox="0 0 12 8"><path d="M1 1l5 5 5-5" stroke="#fff" stroke-width="2" fill="none"/></svg></div>

  <div class="member-ring" style="left:484px;top:168px"><div class="member-photo" role="img" aria-label="Portrait of team member"></div></div>
  <div class="member-name" style="left:485px;top:416px">John Doe</div>
  <div class="member-role" style="left:485px;top:444px">Company name</div>
  <div class="toggle" style="left:662px;top:419px"><svg width="12" height="8" viewBox="0 0 12 8"><path d="M1 1l5 5 5-5" stroke="#fff" stroke-width="2" fill="none"/></svg></div>

  <div class="member-ring" style="left:788px;top:168px"><div class="member-photo" role="img" aria-label="Portrait of team member"></div></div>
  <div class="member-name" style="left:789px;top:416px">John Doe</div>
  <div class="member-role" style="left:789px;top:444px">Company name</div>
  <div class="toggle" style="left:966px;top:419px"><svg width="12" height="8" viewBox="0 0 12 8"><path d="M1 1l5 5 5-5" stroke="#fff" stroke-width="2" fill="none"/></svg></div>
</section>

<div class="abs contact-card">
  <div class="abs" role="img" aria-label="Researcher working with glowing lab equipment" style="left:0;top:0;width:455px;height:323px;border-radius:12px 0 0 12px;background:linear-gradient(135deg,#2c4f86,#5b8ac4 45%,#1a2a55)"></div>
</div>
<h2 class="abs display" style="left:648px;top:3482px;font-size:38px;">Contact <span class="accent">Us</span></h2>
<div class="rule" style="left:648px;top:3545px;width:94px"></div>
<svg class="contact-icon" style="top:3566px" width="16" height="20" viewBox="0 0 16 20"><path d="M8 0a7 7 0 0 0-7 7c0 5 7 13 7 13s7-8 7-13a7 7 0 0 0-7-7z" fill="#2bb8ea"/><circle cx="8" cy="7" r="2.5" fill="#141148"/></svg>
<div class="contact-line" style="top:3563px">123, Lorem ipsum dolor sit</div>
<svg class="contact-icon" style="top:3624px" width="18" height="18" viewBox="0 0 18 18"><path d="M4 1l3 4-2 2c1 3 3 5 6 6l2-2 4 3-2 3C8 17 1 10 1 3z" fill="#2bb8ea"/></svg>
<div class="contact-line" style="top:3620px">+1 888 888 8888</div>
<svg class="contact-icon" style="top:3683px" width="20" height="15" viewBox="0 0 20 15"><rect width="20" height="15" rx="1.5" fill="#2bb8ea"/><path d="M1 1l9 7 9-7" stroke="#141148" stroke-width="1.6" fill="none"/></svg>
<div class="contact-line" style="top:3677px">info@companyname.com</div>

<footer class="abs site-footer">
  <div class="abs brand-name" style="left:0;width:1200px;text-align:center;top:58px;font-size:72px;line-height:90px;">KLARO</div>
  <div class="abs" style="left:144px;top:225px;width:912px;height:1px;background:#4a4690"></div>
  <div class="abs" style="left:0;width:1200px;top:249px;text-align:center;font-size:13px;color:var(--text-soft)">© Copyrights 2025 | All Rights Reserved</div>
</footer>
<nav class="footer-nav">
  <span>HOME</span><span class="sep">/</span><span>ABOUT</span><span class="sep">/</span><span>TECHNOLOGY</span><span class="sep">/</span><span>PUBLICATIONS</span><span class="sep">/</span><span>CONTACT</span>
</nav>

</body>
</html>
```